Website for IT consulting Company

I need a website upgrade, the existing site content is ok, I would also like to add a testimonial page, the site should be something that is easy for us to update content. You use the content from www.kelvanbrook.com as an example. I will also post update logo and artwork. I also need a contact form with some type of validation or captcha.

I added Coded to the Project

Please omit Address maps

Target Market(s)

small business, service oriented companies. We provide IT Consulting, support and mangement

Industry/Entity Type

Information Technology

Coding

Number of Pages Required

1 page

Font styles to use
Serif
Sans Serif

Requirements
Must have
• Contain logo attached, and content from existing web site www.kelvanbrook.com.
• Also need to update content easily, and be movable to different platforms.
• There is a catch phrase
• "Let us worry about your technology…” “ so you don’t have to!”
• Should be included.
Nice to have
• Testimonial page, Project page where we can post new and past projects and pictures
Should not have
• none

```html
<!DOCTYPE html>
<html lang="en">
<head>
<meta charset="utf-8">
<title>Kelvanbrook – IT Consulting</title>
<link href="https://fonts.googleapis.com/css2?family=Roboto:wght@300;400;500;700&family=Open+Sans:wght@400;600;700&display=swap" rel="stylesheet">
<style>
:root{
  --orange:#f07f22;
  --orange-light:#f7a04a;
  --orange-deep:#e0691a;
  --white:#ffffff;
  --ink:#333333;
  --muted:#666666;
  --panel:#f2f2f2;
  --dark:#2f2f2f;
  --darker:#232323;
  --teal:#27a9c4;
}
*{box-sizing:border-box;margin:0;padding:0}
html,body{width:1200px;height:3614px;overflow:hidden}
body{position:relative;font-family:"Open Sans",Arial,sans-serif;color:var(--ink);background:var(--white)}
.abs{position:absolute}
.center{text-align:center}
/* header */
.hero{left:0;top:0;width:1200px;height:687px;background:linear-gradient(100deg,#e9e9ea 0%,#d3d4d6 45%,#b9b6b1 70%,#8d8a86 100%)}
.hero-shade{left:0;top:0;width:700px;height:687px;background:linear-gradient(90deg,rgba(60,60,60,.55),rgba(60,60,60,0))}
.logo-box{left:62px;top:16px;width:320px;height:92px;background:rgba(255,255,255,.92);border-radius:4px;display:flex;align-items:center;gap:12px;padding-left:18px}
.logo-mark{width:34px;height:34px;background:var(--orange)}
.logo-name{font-family:"Roboto",sans-serif;font-weight:700;font-size:34px;color:var(--orange);letter-spacing:1px}
.topbar{left:410px;top:0;width:735px;height:50px;background:var(--orange);border-radius:0 0 24px 24px;display:flex;align-items:center;padding:0 26px;color:var(--white);font-size:17px;gap:18px}
.topbar .item{display:flex;align-items:center;gap:10px}
.topbar .phone{font-family:"Roboto",sans-serif;font-weight:500;font-size:20px}
.topbar .social{margin-left:auto;display:flex;gap:10px}
.dot{width:30px;height:30px;border-radius:50%;border:2px solid var(--white)}
.nav{left:425px;top:72px;display:flex;gap:30px;font-family:"Roboto",sans-serif;font-size:17px;color:#333}
.hero-title{left:80px;top:254px;font-family:"Roboto",sans-serif;font-weight:400;font-size:48px;color:var(--white);letter-spacing:1px}
.hero-tag{left:80px;top:330px;width:560px;font-family:"Roboto",sans-serif;font-size:24px;line-height:34px;color:var(--white)}
.btn{display:inline-block;background:var(--orange);color:var(--white);font-family:"Roboto",sans-serif;font-weight:700;text-transform:uppercase;border-radius:26px}
.hero-btn{left:78px;top:432px;font-size:17px;padding:15px 28px}
/* orange bands */
.band{left:0;width:1200px;background:linear-gradient(180deg,var(--orange-light),var(--orange))}
.band-tab{left:500px;width:200px;height:40px;background:var(--orange-light);border-radius:20px 20px 0 0}
.sec-title{left:0;width:1200px;text-align:center;font-family:"Roboto",sans-serif;font-weight:400;font-size:42px;color:var(--white);letter-spacing:.5px}
.welcome-text{left:130px;top:815px;width:940px;text-align:center;font-size:15px;line-height:27px;color:var(--white)}
.feature{width:330px;text-align:center;color:var(--white)}
.icon-box{width:104px;height:104px;border-radius:10px;background:rgba(255,255,255,.28);border:2px solid rgba(255,255,255,.5);display:flex;align-items:center;justify-content:center;margin:0 auto}
.feature h3{font-family:"Roboto",sans-serif;font-weight:400;font-size:23px;line-height:27px;margin-top:26px}
.feature p{font-size:14px;line-height:24px;margin-top:10px}
.more{font-weight:700;margin-left:6px}
/* about */
.about-img{left:0;top:1176px;width:600px;height:444px;background:linear-gradient(120deg,#2bb3cf 0%,#7fd4e6 35%,#e9d6c8 60%,#b9c4ca 100%)}
.about-panel{left:600px;top:1176px;width:600px;height:444px;background:linear-gradient(90deg,#1c1c1c,#2b2b2b)}
.about-title{left:645px;top:1262px;font-family:"Roboto",sans-serif;font-size:44px;color:var(--white)}
.about-text{left:645px;top:1333px;width:505px;font-size:15px;line-height:28px;color:#e6e6e6}
.about-btn{left:638px;top:1482px;font-size:17px;padding:12px 26px;border-radius:6px}
/* support */
.support{left:0;top:1620px;width:1200px;height:585px;background:linear-gradient(180deg,rgba(240,127,34,.92),rgba(232,110,26,.96)),linear-gradient(90deg,#c9a27a,#f3cfa8)}
.support-hand{left:470px;top:1880px;width:200px;height:325px;border-radius:100px 100px 0 0;background:linear-gradient(180deg,rgba(255,225,200,.55),rgba(255,205,170,.35))}
.svc{display:flex;align-items:center;gap:22px;color:var(--white);font-family:"Roboto",sans-serif;font-size:22px}
.svc.left{justify-content:flex-end;text-align:right;width:420px}
.svc .icon-box{margin:0;width:102px;height:102px;flex:none}
/* projects */
.projects{left:0;top:2205px;width:1200px;height:603px;background:var(--panel)}
.proj-title{left:0;top:2256px;width:1200px;text-align:center;font-family:"Roboto",sans-serif;font-size:42px;color:#555}
.proj-title span{color:var(--orange)}
.proj-sub{left:0;top:2328px;width:1200px;text-align:center;font-size:15px;line-height:26px;color:var(--muted)}
.tile{display:flex;flex-direction:column;align-items:center;justify-content:center;gap:16px;background:linear-gradient(180deg,var(--orange-light),var(--orange));color:var(--white);font-family:"Roboto",sans-serif;font-size:23px;line-height:26px;text-align:center}
.tile .learn{background:var(--white);color:var(--orange);font-size:14px;padding:9px 22px;border-radius:3px;text-transform:uppercase}
.photo{background:linear-gradient(135deg,#b9bcc0,#6e7378)}
.photo.dark{background:linear-gradient(135deg,#4a4d52,#1f2124)}
.photo.warm{background:linear-gradient(135deg,#d9cfc4,#8d847b)}
/* testimonials */
.testi{left:0;top:2808px;width:1200px;height:433px;background:linear-gradient(180deg,rgba(247,160,74,.95),rgba(240,127,34,.98))}
.quote-mark{left:570px;top:2983px;width:60px;height:60px;border-radius:50%;border:3px solid var(--white);color:var(--white);font-family:Georgia,serif;font-size:52px;line-height:72px;text-align:center}
.testi-text{left:150px;top:3050px;width:900px;text-align:center;font-size:15px;line-height:29px;color:var(--white)}
.arrow{width:36px;height:36px;border-radius:50%;border:2px solid var(--white);display:flex;align-items:center;justify-content:center}
.avatar{left:484px;top:3132px;width:80px;height:80px;border-radius:50%;background:linear-gradient(180deg,#e7e2dc,#b7aea5);border:3px solid var(--white)}
.client{left:580px;top:3160px;font-size:17px;color:var(--white)}
/* footer */
.footer{left:0;top:3241px;width:1200px;height:326px;background:linear-gradient(90deg,#3a3a3a,var(--dark) 50%,var(--darker))}
.foot-logo{left:72px;top:3345px;display:flex;align-items:center;gap:10px}
.foot-logo .logo-mark{width:26px;height:26px}
.foot-logo .logo-name{font-size:26px;color:var(--white)}
.foot-social{left:72px;top:3480px;display:flex;gap:18px}
.foot-social .dot{width:50px;height:50px;border:none;background:var(--orange)}
.foot-social .dot.w{background:var(--white)}
.col-title{font-family:"Roboto",sans-serif;font-size:21px;color:var(--white)}
.links{left:350px;top:3310px}
.links ul{list-style:none;margin-top:20px;font-size:15px;line-height:23px;color:#ddd}
.news{left:620px;top:3310px;width:230px}
.field{width:232px;height:50px;border:1px solid #cfcfcf;color:#eee;font-size:15px;padding:14px 10px;margin-top:14px}
.subscribe{display:inline-block;margin-top:20px;background:var(--white);color:var(--orange);font-family:"Roboto",sans-serif;font-weight:700;font-size:17px;padding:10px 18px}
.contact{left:890px;top:3310px;width:260px}
.contact .row{display:flex;gap:10px;margin-top:16px;font-size:15px;line-height:21px;color:#ddd}
.contact .row.first{margin-top:24px}
.contact b{color:var(--white)}
.copy{left:0;top:3567px;width:1200px;height:47px;background:var(--orange);color:var(--white);font-size:15px;text-align:center;line-height:47px}
</style>
</head>
<body>

<!-- Header and hero -->
<div class="abs hero" role="img" aria-label="Photo of a thoughtful man in glasses at a laptop in a bright office"></div>
<div class="abs hero-shade"></div>
<div class="abs logo-box"><span class="logo-mark"></span><span class="logo-name">KELVANBROOK</span></div>
<div class="abs topbar">
  <span class="item phone">
    <svg width="24" height="24" viewBox="0 0 24 24"><circle cx="12" cy="12" r="11" fill="none" stroke="#fff" stroke-width="2"/><path d="M8 7l2 0 1 3-1.5 1a6 6 0 0 0 3.5 3.5l1-1.5 3 1v2c-5 1-10-4-9-9z" fill="#fff"/></svg>
    (555) 014-2280</span>
  <span class="item">
    <svg width="24" height="24" viewBox="0 0 24 24"><circle cx="12" cy="12" r="11" fill="none" stroke="#fff" stroke-width="2"/><rect x="6" y="8" width="12" height="8" fill="none" stroke="#fff" stroke-width="1.5"/><path d="M6 8l6 5 6-5" fill="none" stroke="#fff" stroke-width="1.5"/></svg>
    info@kelvanbrookgroup.com</span>
  <span class="social"><span class="dot"></span><span class="dot"></span><span class="dot"></span></span>
</div>
<nav class="abs nav"><span>Home</span><span>About</span><span>Projects</span><span>Support</span><span>Clients</span><span>Careers</span><span>Testimonials</span><span>Contact</span></nav>
<h1 class="abs hero-title">KELVANBROOK.COM</h1>
<p class="abs hero-tag">Let us worry about your technology... So you don't have to !</p>
<span class="abs btn hero-btn">Contact us now</span>

<!-- Welcome -->
<div class="abs band-tab" style="top:647px"></div>
<section class="abs band" style="top:687px;height:489px;border-radius:30px 30px 0 0"></section>
<h2 class="abs sec-title" style="top:745px">WELCOME TO KELVANBROOK.COM</h2>
<p class="abs welcome-text">Outsourcing is subcontracting a process, such as product design or manufacturing, to a third-party company.[1] The decision to outsource is often made in the interest of lowering firm costs, redirecting or conserving energy directed at the competencies of a particular business, or to make more efficient use of land, labor, capital, (information) technology and resources.</p>

<div class="abs feature" style="left:75px;top:928px">
  <div class="icon-box"><svg width="60" height="60" viewBox="0 0 60 60"><circle cx="24" cy="34" r="12" fill="none" stroke="#fff" stroke-width="7" stroke-dasharray="5 4"/><circle cx="24" cy="34" r="5" fill="#fff"/><circle cx="44" cy="16" r="7" fill="none" stroke="#fff" stroke-width="5" stroke-dasharray="3 3"/></svg></div>
  <h3>Managed IT Solutions</h3>
  <p>Our staff will design, service, administer and maintain your IT needs. We are well versed on all...<span class="more">READ MORE &raquo;</span></p>
</div>
<div class="abs feature" style="left:435px;top:928px">
  <div class="icon-box"><svg width="60" height="60" viewBox="0 0 60 60"><rect x="12" y="14" width="36" height="24" rx="2" fill="none" stroke="#fff" stroke-width="3"/><path d="M8 44h44" stroke="#fff" stroke-width="4"/><path d="M22 30l6-6 4 4 8-8" fill="none" stroke="#fff" stroke-width="3"/></svg></div>
  <h3>Remote Diagnostic and Support</h3>
  <p>Do you need a quick solution to a technical problem? With our...<span class="more">READ MORE &raquo;</span></p>
</div>
<div class="abs feature" style="left:795px;top:928px">
  <div class="icon-box"><svg width="60" height="60" viewBox="0 0 60 60"><rect x="10" y="12" width="22" height="30" rx="11" fill="none" stroke="#fff" stroke-width="3"/><path d="M21 12v10" stroke="#fff" stroke-width="3"/><path d="M32 30c8 0 10 6 16 6" fill="none" stroke="#fff" stroke-width="3"/></svg></div>
  <h3>IT Infrastructure Design and Installation</h3>
  <p>Do you have more than one site? Do you need remote...<span class="more">READ MORE &raquo;</span></p>
</div>

<!-- About -->
<div class="abs about-img" role="img" aria-label="Close-up of a woman wearing a futuristic visor with digital interface graphics"></div>
<div class="abs about-panel"></div>
<h2 class="abs about-title">ABOUT US</h2>
<p class="abs about-text">Our clients choose Kelvanbrook and stay with us because we deliver on every technology need they have. We have a 90% client retention rate. Many of our clients span ten or more years. Whether you need to completely outsource your IT requirements or add advanced insight to your existing IT department, Kelvanbrook can serve...</p>
<span class="abs btn about-btn">Read more &raquo;</span>

<!-- IT support solutions -->
<div class="abs band-tab" style="top:1585px;background:var(--orange)"></div>
<section class="abs support" role="img" aria-label="Background photo of a hand touching a digital screen in an office"></section>
<div class="abs support-hand"></div>
<h2 class="abs sec-title" style="top:1672px">IT SUPPORT SOLUTIONS</h2>

<div class="abs svc left" style="left:0;top:1768px"><span>Network<br>Administration</span><span class="icon-box"><svg width="54" height="54" viewBox="0 0 60 60"><circle cx="24" cy="34" r="12" fill="none" stroke="#fff" stroke-width="7" stroke-dasharray="5 4"/><circle cx="44" cy="16" r="7" fill="none" stroke="#fff" stroke-width="5" stroke-dasharray="3 3"/></svg></span></div>
<div class="abs svc left" style="left:0;top:1912px"><span>Desktop Support</span><span class="icon-box"><svg width="54" height="54" viewBox="0 0 60 60"><rect x="10" y="12" width="40" height="28" rx="2" fill="none" stroke="#fff" stroke-width="3"/><path d="M6 46h48" stroke="#fff" stroke-width="4"/><path d="M22 20l16 14M38 20L22 34" stroke="#fff" stroke-width="3"/></svg></span></div>
<div class="abs svc left" style="left:0;top:2056px"><span>Network Cabling</span><span class="icon-box"><svg width="54" height="54" viewBox="0 0 60 60"><rect x="18" y="12" width="34" height="26" rx="2" fill="none" stroke="#fff" stroke-width="3"/><path d="M30 38v8h-6M35 46h-11" stroke="#fff" stroke-width="3"/><path d="M8 20h8v10H8z" fill="#fff"/></svg></span></div>

<div class="abs svc" style="left:783px;top:1768px"><span class="icon-box"><svg width="54" height="54" viewBox="0 0 60 60"><path d="M10 26a28 28 0 0 1 40 0M17 33a18 18 0 0 1 26 0M24 40a8 8 0 0 1 12 0" fill="none" stroke="#fff" stroke-width="4"/><circle cx="30" cy="47" r="3" fill="#fff"/></svg></span><span>Wireless Networks</span></div>
<div class="abs svc" style="left:783px;top:1912px"><span class="icon-box"><svg width="54" height="54" viewBox="0 0 60 60"><path d="M30 8l18 7v14c0 12-9 19-18 23-9-4-18-11-18-23V15z" fill="none" stroke="#fff" stroke-width="3"/><path d="M22 30l6 6 11-12" fill="none" stroke="#fff" stroke-width="4"/></svg></span><span>Antivirus Solutions</span></div>
<div class="abs svc" style="left:783px;top:2056px"><span class="icon-box"><svg width="54" height="54" viewBox="0 0 60 60"><circle cx="16" cy="18" r="6" fill="none" stroke="#fff" stroke-width="3"/><circle cx="44" cy="30" r="6" fill="none" stroke="#fff" stroke-width="3"/><circle cx="18" cy="44" r="6" fill="none" stroke="#fff" stroke-width="3"/><path d="M21 21l17 7M22 40l17-7M16 24v14" stroke="#fff" stroke-width="3"/></svg></span><span>Network Security</span></div>

<!-- Projects -->
<section class="abs projects"></section>
<h2 class="abs proj-title">OUR <span>PROJECTS</span></h2>
<p class="abs proj-sub">Lorem Ipsum is simply dummy text of the printing and typesetting industry.<br>Lorem Ipsum has a been the industry's standard.</p>

<div class="abs tile" style="left:96px;top:2424px;width:241px;height:167px">Web Design<span class="learn">Learn more</span></div>
<div class="abs photo dark" style="left:96px;top:2612px;width:241px;height:157px" role="img" aria-label="Project photo of a laptop showing a welcome screen on a desk"></div>
<div class="abs photo" style="left:361px;top:2424px;width:241px;height:114px" role="img" aria-label="Project photo of hands typing on a laptop"></div>
<div class="abs tile" style="left:361px;top:2562px;width:241px;height:207px">Antivirus<br>Solutions<span class="learn">Learn more</span></div>
<div class="abs tile" style="left:627px;top:2424px;width:241px;height:184px">Network<br>Security<span class="learn">Learn more</span></div>
<div class="abs photo warm" style="left:627px;top:2629px;width:241px;height:140px" role="img" aria-label="Project photo of a man working at a laptop"></div>
<div class="abs photo warm" style="left:894px;top:2424px;width:243px;height:140px" role="img" aria-label="Project photo of a workstation with laptop and monitor"></div>
<div class="abs tile" style="left:894px;top:2588px;width:243px;height:181px">Antivirus<br>Solutions<span class="learn">Learn more</span></div>

<!-- Testimonials -->
<div class="abs band-tab" style="top:2790px;height:30px"></div>
<section class="abs testi" role="img" aria-label="Background photo of a person working at a desk, tinted orange"></section>
<h2 class="abs sec-title" style="top:2908px">WHAT OUR CLIENT SAY</h2>
<div class="abs quote-mark">&ldquo;</div>
<p class="abs testi-text">Lorem Ipsum is simply dummy text of the printing and typesetting industry. Lorem Ipsum has been the industry's standard dummy text ever since the 1500s, when an unknown printer took a galley of type and scrambled it to make a type specimen book. It has survived not only five centuries, but also the leap into electronic type setting.</p>
<div class="abs arrow" style="left:76px;top:3058px"><svg width="14" height="14" viewBox="0 0 14 14"><path d="M9 2L4 7l5 5" fill="none" stroke="#fff" stroke-width="2"/></svg></div>
<div class="abs arrow" style="left:1088px;top:3058px"><svg width="14" height="14" viewBox="0 0 14 14"><path d="M5 2l5 5-5 5" fill="none" stroke="#fff" stroke-width="2"/></svg></div>
<div class="abs avatar" role="img" aria-label="Client portrait photo"></div>
<span class="abs client">- Client Name</span>

<!-- Footer -->
<footer class="abs footer"></footer>
<div class="abs foot-logo"><span class="logo-mark"></span><span class="logo-name">KELVANBROOK</span></div>
<div class="abs foot-social"><span class="dot"></span><span class="dot w"></span><span class="dot w"></span></div>

<div class="abs links"><div class="col-title">Useful Links</div>
  <ul><li>Home</li><li>About</li><li>Projects</li><li>Support</li><li>Clients</li><li>Careers</li><li>Testimonials</li><li>Contact</li></ul>
</div>
<div class="abs news"><div class="col-title">Newsletter</div>
  <div class="field" style="margin-top:20px">Enter Name</div>
  <div class="field">Enter Email</div>
  <span class="subscribe">SUBSCRIBE</span>
</div>
<div class="abs contact"><div class="col-title">Get In Touch With Us</div>
  <div class="row first"><svg width="16" height="20" viewBox="0 0 16 20"><path d="M8 1a6 6 0 0 0-6 6c0 5 6 12 6 12s6-7 6-12a6 6 0 0 0-6-6z" fill="#fff"/><circle cx="8" cy="7" r="2.2" fill="#333"/></svg><span>123 Building name,<br>City, Country - Zipcode</span></div>
  <div class="row"><svg width="16" height="18" viewBox="0 0 24 24"><path d="M5 3h4l2 5-2.5 1.5a11 11 0 0 0 6 6L16 13l5 2v4c-9 2-18-7-16-16z" fill="#fff"/></svg><b>555.014.2280</b></div>
  <div class="row"><svg width="16" height="16" viewBox="0 0 16 16"><rect x="1" y="3" width="14" height="10" fill="none" stroke="#fff" stroke-width="1.5"/><path d="M1 3l7 6 7-6" fill="none" stroke="#fff" stroke-width="1.5"/></svg><span>info@kelvanbrook<br>group.com</span></div>
  <div class="row"><svg width="16" height="16" viewBox="0 0 16 16"><circle cx="8" cy="8" r="7" fill="none" stroke="#fff" stroke-width="1.5"/><path d="M1 8h14M8 1c-4 4-4 10 0 14M8 1c4 4 4 10 0 14" fill="none" stroke="#fff" stroke-width="1.2"/></svg><span>www.kelvanbrook.com</span></div>
</div>
<div class="abs copy">&copy; <b>KELVANBROOK.COM</b> - 2017. All Rights Reserved.</div>

</body>
</html>
```